Corvane Capital Business Cards

These are professional business cards that are for my family office.
Put fake emails and phone numbers as of now until I finalize those components. This family office controls my families investments, assets, and future. The cards should be professional.
..
.
.
.
I just uploaded another variation of a logo I would like to see as a business card to I am inbeteen which logo to use

Target Market(s)

business

Industry/Entity Type

business

Contact Information for Business Card

Professional, wealth related, finance related.

Requirements
Must have
• Logo

```html
<!DOCTYPE html>
<html lang="en">
<head>
<meta charset="utf-8">
<title>Corvane Capital – Business Cards</title>
<link href="https://fonts.googleapis.com/css2?family=Playfair+Display:wght@400;600&family=Arimo:wght@400&display=swap" rel="stylesheet">
<style>
  :root {
    --page: #1a1a1a;
    --card: #262626;
    --gold: #c4a96b;
    --white: #ffffff;
    --muted: #e6e6e6;
    --serif: "Playfair Display", Georgia, serif;
    --sans: "Arimo", Arial, sans-serif;
  }
  * { box-sizing: border-box; margin: 0; padding: 0; }
  html, body { width: 1200px; height: 900px; overflow: hidden; }
  body {
    background: var(--page);
    display: flex;
    flex-direction: column;
    align-items: center;
    justify-content: center;
    gap: 60px;
  }
  .card {
    position: relative;
    width: 630px;
    height: 360px;
    background: var(--card);
    border-radius: 18px;
    overflow: hidden;
    box-shadow: 0 12px 30px rgba(0,0,0,.5);
  }

  /* Front */
  .card-front {
    display: flex;
    align-items: center;
    justify-content: center;
  }
  .brand {
    display: flex;
    align-items: center;
    gap: 16px;
  }
  .brand-mark {
    width: 22px;
    height: 22px;
    background: var(--gold);
  }
  .brand-name {
    font-family: var(--serif);
    font-weight: 400;
    color: var(--white);
    letter-spacing: .06em;
    text-transform: uppercase;
    font-size: 38px;
  }

  /* Back */
  .card-back .brand {
    position: absolute;
    left: 44px;
    top: 70px;
    gap: 12px;
  }
  .card-back .brand-mark { width: 16px; height: 16px; }
  .card-back .brand-name { font-size: 28px; }

  .holder {
    position: absolute;
    right: 44px;
    top: 34px;
    text-align: right;
  }
  .holder-name {
    font-family: var(--serif);
    font-weight: 600;
    color: var(--gold);
    font-size: 22px;
    letter-spacing: .05em;
    text-transform: uppercase;
  }
  .holder-title {
    font-family: var(--sans);
    color: var(--white);
    font-size: 14px;
    margin-top: 2px;
  }
  .holder-bar {
    position: absolute;
    right: 0;
    top: 34px;
    width: 12px;
    height: 44px;
    background: var(--gold);
  }

  .address {
    position: absolute;
    left: 50px;
    top: 160px;
    font-family: var(--sans);
    color: var(--white);
    font-size: 16px;
    line-height: 1.35;
  }
  .contacts {
    position: absolute;
    left: 50px;
    top: 228px;
    list-style: none;
    font-family: var(--sans);
    color: var(--white);
    font-size: 16px;
  }
  .contacts li {
    display: flex;
    align-items: center;
    gap: 10px;
    height: 26px;
  }
  .contacts svg { width: 14px; height: 14px; fill: var(--gold); flex: none; }

  .decor-square {
    position: absolute;
    right: 70px;
    top: 130px;
    width: 150px;
    height: 150px;
    background: linear-gradient(160deg, #1d1d1d 0%, #3a3a3a 100%);
  }

  .edge-band {
    position: absolute;
    left: 0;
    right: 0;
    bottom: 0;
    height: 8px;
    display: flex;
  }
  .edge-band .band-gold { flex: 0 0 58%; background: var(--gold); }
  .edge-band .band-white { flex: 1; background: var(--white); }
</style>
</head>
<body>

  <section class="card card-front" aria-label="Card front">
    <div class="brand">
      <span class="brand-mark"></span>
      <span class="brand-name">Corvane Capital</span>
    </div>
  </section>

  <section class="card card-back" aria-label="Card back">
    <div class="holder">
      <p class="holder-name">Elliot Marsh</p>
      <p class="holder-title">CEO/Founder</p>
    </div>
    <span class="holder-bar"></span>

    <div class="brand">
      <span class="brand-mark"></span>
      <span class="brand-name">Corvane Capital</span>
    </div>

    <p class="address">4820 Linden Ridge Rd Suite 200<br>Fairhaven, AB 550318</p>

    <ul class="contacts">
      <li>
        <svg viewBox="0 0 16 16" aria-hidden="true"><path d="M3.5 1l2.5 3-1.5 1.5c.8 1.8 2.2 3.2 4 4L10 8l3 2.5-1.5 3C6 13 3 10 2 4.5z"/></svg>
        (555) 014-3377
      </li>
      <li>
        <svg viewBox="0 0 16 16" aria-hidden="true"><path d="M1 3h14v10H1zm1.5 1.2v.4L8 8.5l5.5-3.9v-.4z"/></svg>
        ElliotM@corvanecapital.com
      </li>
      <li>
        <svg viewBox="0 0 16 16" aria-hidden="true"><path d="M8 1a7 7 0 1 0 0 14A7 7 0 0 0 8 1zm0 1.5c.9 0 1.9 1.9 2.1 4.5H5.9C6.1 4.4 7.1 2.5 8 2.5zM2.6 8.5h2.3c.1 1.8.5 3.3 1.1 4.3a5.6 5.6 0 0 1-3.4-4.3zm0-1.5A5.6 5.6 0 0 1 6 3.2C5.4 4.2 5 5.6 4.9 7zm3.3 1.5h4.2c-.2 2.6-1.2 4.5-2.1 4.5s-1.9-1.9-2.1-4.5zm5.2 0h2.3A5.6 5.6 0 0 1 10 12.8c.6-1 1-2.5 1.1-4.3zm0-1.5c-.1-1.4-.5-2.8-1.1-3.8a5.6 5.6 0 0 1 3.4 3.8z"/></svg>
        www.corvanecapital.com
      </li>
    </ul>

    <span class="decor-square" aria-hidden="true"></span>

    <div class="edge-band" aria-hidden="true">
      <span class="band-gold"></span>
      <span class="band-white"></span>
    </div>
  </section>

</body>
</html>
```